Design Startseite Kanzlei-Homepage
Zielgruppe
Wir sind eine Rechtsanwaltskanzlei in Kempten (Allgäu) und regional sowie überregional in verschiedenen Rechtsgebieten tätig. Unsere Zielgruppe sind sowohl private als auch gewerbliche Mandanten.
Aufgabenstellung
Die bestehende Gestaltung wirkt derzeit aus unserer Sicht überholt. Insbesondere soll das bislang dominierende Rot vollständig entfallen.
Stattdessen stellen wir uns ein modernes, hochwertiges Erscheinungsbild vor, primär in dunklen Farbtönen (Anthrazit/Schwarz) kombiniert mit Beige- bzw. warmen Naturtönen. Ziel ist eine klare visuelle Anlehnung an unsere Kanzleiräumlichkeiten (siehe Fotos).
Die Webseite soll insgesamt moderner, klarer und visuell anspruchsvoller wirken, ohne an Seriosität und Zugänglichkeit einzubüßen. Die Balance zwischen hochwertigem Erscheinungsbild und mandantenorientierter Nutzerführung steht für uns im Vordergrund.

```html
<!DOCTYPE html>
<html lang="de">
<head>
<meta charset="utf-8">
<title>Kanzlei am Lindenhof – Startseite</title>
<link href="https://fonts.googleapis.com/css2?family=Gelasio:wght@400;500&family=Roboto:wght@400;500;700&display=swap" rel="stylesheet">
<style>
:root{
  --ink:#1c1c1c;
  --panel:#262626;
  --panel-line:#3a3a3a;
  --gold:#a8845a;
  --beige:#dcc3a0;
  --cream:#f3efe9;
  --cream-2:#ede4dc;
  --white:#ffffff;
  --text:#222222;
  --muted:#555555;
  --star:#f2b01e;
}
*{box-sizing:border-box;margin:0;padding:0}
html,body{width:1200px;height:3211px;overflow:hidden}
body{font-family:"Roboto",Arial,sans-serif;color:var(--text);background:var(--cream);position:relative}
.serif{font-family:"Gelasio",Georgia,serif;font-weight:400}
a{color:inherit;text-decoration:none}
.btn{display:inline-flex;align-items:center;justify-content:center;height:50px;padding:0 12px;font-size:15px;font-weight:500;border-radius:2px;white-space:nowrap}
.btn-beige{background:var(--beige);color:#1e1e1e}
.btn-outline{border:1px solid #fff;color:#fff}
.btn-dark{background:var(--ink);color:#fff}
.eyebrow{font-size:16px;letter-spacing:1.4px;font-weight:500;color:var(--gold);text-transform:uppercase}
.rule{width:44px;height:2px;background:#c9b49a}

/* nav */
.nav{position:absolute;top:0;left:0;width:1200px;height:77px;background:var(--ink);display:flex;align-items:center;padding:0 87px;z-index:2}
.brand{font-size:22px;font-weight:700;color:#fff;letter-spacing:.5px}
.menu{display:flex;gap:44px;margin-left:auto;margin-right:44px;font-size:15px;color:#fff}
.menu .active{color:var(--beige);font-weight:500}
.nav .btn{height:50px;font-size:14px;padding:0 12px}

/* hero */
.hero{position:absolute;top:77px;left:0;width:1200px;height:596px;background:linear-gradient(90deg,#2a1c10 0%,#5b3d21 28%,#7a5632 45%,#3c2c1e 60%,#2a2622 100%)}
.hero-photo{position:absolute;inset:0;background:linear-gradient(180deg,rgba(0,0,0,.1),rgba(0,0,0,.35))}
.hero-content{position:absolute;left:87px;top:92px;width:500px;color:#fff}
.hero h1{font-size:66px;line-height:72px}
.hero .eyebrow{color:var(--beige);margin-top:22px;font-size:15.5px}
.hero .rule{margin-top:14px}
.hero p{margin-top:28px;font-size:16px;line-height:24px;width:390px}
.hero .actions{display:flex;gap:15px;margin-top:40px}
.stats{position:absolute;right:88px;top:514px;display:flex;gap:34px;color:#fff;font-size:16px;line-height:24px}
.stat{display:flex;gap:14px;align-items:center}

/* intro */
.intro{position:absolute;top:673px;left:0;width:1200px;height:414px;background:#fff}
.intro-text{position:absolute;left:87px;top:50px;width:500px}
.intro h2{font-size:40px;line-height:46px;margin-top:6px}
.intro .rule{margin-top:20px}
.intro p{margin-top:28px;font-size:16px;line-height:24px;width:390px}
.intro .btn{margin-top:36px}
.intro-video{position:absolute;left:605px;top:9px;width:595px;height:396px;background:linear-gradient(180deg,#3c4a5e 0%,#6a6052 55%,#2a2b2f 100%)}
.intro-video svg{position:absolute;left:258px;top:140px}

/* areas */
.areas{position:absolute;top:1087px;left:0;width:1200px;height:695px;background:var(--ink)}
.areas h2{color:#fff;text-align:center;font-size:40px;margin-top:52px}
.grid{position:absolute;left:88px;top:129px;display:grid;grid-template-columns:repeat(3,333px);gap:12px 12px}
.card{height:240px;background:var(--panel);border:1px solid var(--panel-line);padding:32px 20px 0}
.card-head{display:flex;align-items:center;gap:16px;height:70px}
.card-head h3{color:var(--gold);font-size:17px;font-weight:500;line-height:20px}
.card p{color:#e8e8e8;font-size:14px;line-height:22px;margin-top:20px;width:292px}

/* team */
.team{position:absolute;top:1782px;left:0;width:1200px;height:769px;background:var(--cream)}
.team h2{text-align:center;font-size:40px;margin-top:52px}
.team .eyebrow{text-align:center;margin-top:12px}
.people{position:absolute;top:160px;left:87px;display:flex;gap:42px}
.person{width:225px}
.portrait{width:225px;height:291px}
.person h3{font-size:19px;font-weight:500;margin-top:30px;white-space:nowrap}
.person .role{font-size:16.5px;line-height:24px;color:#333;margin-top:12px;height:84px;white-space:nowrap}
.person .more{display:block;margin-top:10px;color:var(--gold);font-weight:500;font-size:16px}
.team .all{position:absolute;left:499px;top:670px;width:203px}

/* reviews */
.reviews{position:absolute;top:2551px;left:0;width:1200px;height:324px;background:var(--cream-2)}
.rv-intro{position:absolute;left:87px;top:34px}
.rv-intro h2{font-size:40px;line-height:45px}
.rv-intro .label{margin-top:38px;font-size:15px;font-weight:500;letter-spacing:.5px}
.rv-intro .based{font-size:15px;margin-top:6px}
.platform{display:flex;align-items:center;gap:8px;margin-top:12px;font-size:24px;font-weight:500;color:#4a4a4a}
.platform span{width:18px;height:18px;border-radius:50%;background:#4a4a4a}
.review{position:absolute;top:25px;width:335px;height:276px;background:var(--cream);border:1px solid #e2d7cc;padding:22px 22px}
.review p{margin-top:16px;font-size:13.5px;line-height:22.5px;color:#222}
.review .by{margin-top:12px;font-size:13.5px;font-weight:700}
.arrow{position:absolute;top:145px}

/* contact */
.contact{position:absolute;top:2875px;left:0;width:1200px;height:336px;background:var(--ink);color:#fff}
.contact h2{position:absolute;left:87px;top:60px;font-size:40px}
.contact .lead{position:absolute;left:87px;top:124px;width:260px;font-size:14px;line-height:20px}
.contact .btn{position:absolute;left:87px;top:216px;width:203px}
.channels{position:absolute;left:518px;top:80px;font-size:17px;letter-spacing:1.2px;color:var(--beige);font-weight:500}
.channels div{display:flex;align-items:center;gap:14px;height:40px}
.address{position:absolute;left:864px;top:88px;font-size:16.5px;line-height:26px}
.address a{display:inline-block;margin-top:14px;color:var(--beige);text-decoration:underline}
</style>
</head>
<body>

<header class="nav">
  <div class="brand">KANZLEI AM LINDENHOF</div>
  <nav class="menu">
    <a class="active">Startseite</a>
    <a>Rechtsgebiete &#8964;</a>
    <a>Kanzlei &#8964;</a>
    <a>Kontakt</a>
  </nav>
  <a class="btn btn-beige">Erstberatung anfragen</a>
</header>

<section class="hero">
  <div class="hero-photo" role="img" aria-label="Empfangsbereich der Kanzlei mit Holzvertäfelung und beleuchtetem Empfangstresen"></div>
  <div class="hero-content">
    <h1 class="serif">Rechtsberatung mit Weitblick.</h1>
    <div class="eyebrow">Für Privatpersonen und Untermehmen.</div>
    <div class="rule"></div>
    <p>Lorem ipsum dolor sit amet, consetetur sadipscing elitr, sed diam nonumy eirmod tempor invidunt ut labore et dolore magna aliquyam erat.</p>
    <div class="actions">
      <a class="btn btn-beige" style="width:203px">Erstberatung anfragen</a>
      <a class="btn btn-outline" style="width:203px">Rechtsgebiete entdecken</a>
    </div>
  </div>
  <div class="stats">
    <div class="stat">
      <svg width="26" height="38" viewBox="0 0 26 38" fill="none" stroke="#fff" stroke-width="3"><circle cx="13" cy="12" r="9"/><path d="M7 20v15l6-4 6 4V20" fill="#fff"/></svg>
      <div>Über XX Jahre<br>Erfahrung</div>
    </div>
    <div class="stat">
      <svg width="36" height="30" viewBox="0 0 36 30" fill="#fff"><circle cx="11" cy="8" r="6"/><circle cx="25" cy="8" r="6"/><path d="M0 30c0-9 5-14 11-14s11 5 11 14zM16 30c1-9 4-14 9-14 6 0 11 5 11 14z"/></svg>
      <div>XX<br>Fachanwälte</div>
    </div>
    <div class="stat">
      <svg width="36" height="34" viewBox="0 0 36 34" fill="#fff"><path d="M18 0L36 9H0z"/><rect x="2" y="11" width="32" height="3"/><rect x="5" y="15" width="3" height="13"/><rect x="12" y="15" width="3" height="13"/><rect x="21" y="15" width="3" height="13"/><rect x="28" y="15" width="3" height="13"/><rect x="0" y="30" width="36" height="4"/></svg>
      <div>Regional im Allgäu<br>und darüber hinaus</div>
    </div>
  </div>
</section>

<section class="intro">
  <div class="intro-text">
    <div class="eyebrow">Kanzlei am Lindenhof</div>
    <h2 class="serif">Ihre Kanzlei in Kempten<br>für alle rechtlichen Fragen.</h2>
    <div class="rule"></div>
    <p>Lorem ipsum dolor sit amet, consetetur sadipscing elitr, sed diam nonumy eirmod tempor invidunt ut labore et dolore magna aliquyam erat.</p>
    <a class="btn btn-dark" style="width:203px">Mehr über unsere Kanzlei</a>
  </div>
  <div class="intro-video" role="img" aria-label="Video: Kanzleigebäude bei Abenddämmerung">
    <svg width="80" height="110" viewBox="0 0 80 110"><path d="M4 4L76 55 4 106z" fill="rgba(255,255,255,.75)"/></svg>
  </div>
</section>

<section class="areas">
  <h2 class="serif">Kompetenz in verschiedenen Rechtsgebieten.</h2>
  <div class="grid">
    <article class="card">
      <div class="card-head">
        <svg width="72" height="70" viewBox="0 0 72 70" fill="none" stroke="#fff" stroke-width="2.5"><circle cx="18" cy="18" r="7"/><circle cx="52" cy="12" r="7"/><circle cx="36" cy="32" r="5"/><path d="M6 68V38c0-7 5-11 12-11s12 4 12 11v30M40 68V30c0-7 5-11 12-11s12 4 12 11v38M30 68V48c0-4 3-6 6-6s6 2 6 6v20"/></svg>
        <h3>Familienrecht</h3>
      </div>
      <p>Wir beraten und vertreten Sie bei sämtlichen Fragestellungen rund um Ehe und Scheidung, Umgangs- und Sorgerecht sowie Unterhaltszahlungen.</p>
    </article>
    <article class="card">
      <div class="card-head">
        <svg width="80" height="70" viewBox="0 0 80 70" fill="none" stroke="#fff" stroke-width="2.5"><circle cx="22" cy="26" r="10"/><circle cx="52" cy="16" r="12"/><path d="M2 66c0-14 9-22 20-22s20 8 20 22zM30 66c0-18 10-28 22-28s24 10 24 28z"/></svg>
        <h3>Arbeitsrecht</h3>
      </div>
      <p>Wir fungieren sowohl für Arbeitnehmer als auch für Arbeitgeber als Ansprechpartner beim Abschluss und der Auflösung von Arbeitsverträgen.</p>
    </article>
    <article class="card">
      <div class="card-head">
        <svg width="72" height="70" viewBox="0 0 72 70" fill="none" stroke="#fff" stroke-width="2.5"><path d="M14 30l6-16h32l6 16"/><rect x="4" y="30" width="64" height="20" rx="5"/><circle cx="18" cy="40" r="4"/><circle cx="54" cy="40" r="4"/><path d="M28 40h16M10 50v8h10v-8M52 50v8h10v-8"/></svg>
        <h3>Verkehrsrecht</h3>
      </div>
      <p>Wir unterstützen Sie dabei, Ihr Schmerzensgeld oder die Entschädigungszahlung für einen Sachschaden zu bekommen.</p>
    </article>
    <article class="card">
      <div class="card-head">
        <svg width="72" height="70" viewBox="0 0 72 70"><text x="36" y="60" text-anchor="middle" font-family="Georgia,serif" font-size="66" fill="#fff">§</text></svg>
        <h3>Strafrecht</h3>
      </div>
      <p>Wenn Ihnen Post von der Staatsanwaltschaft ins Haus flattert, &nbsp;stehen wir Ihnen mit kompetenter Rechtsberatung zur Seite.</p>
    </article>
    <article class="card">
      <div class="card-head">
        <svg width="72" height="70" viewBox="0 0 72 70" fill="none" stroke="#fff" stroke-width="2.5"><path d="M18 4h44c-6 0-8 6-8 10v44c0 5-4 8-8 8H10c5 0 8-3 8-8V14c0-5 2-10 8-10"/><path d="M26 18h20M26 28h20M26 38h20M26 48h14"/></svg>
        <h3>Erbrecht</h3>
      </div>
      <p>Das Erbrecht ist komplex. Wir beraten und vertreten (potenzielle) Erben und Erblasser vor und nach dem Erbfall in allen rechtlichen Fragen.</p>
    </article>
    <article class="card">
      <div class="card-head">
        <svg width="80" height="70" viewBox="0 0 80 70" fill="none" stroke="#fff" stroke-width="2.5"><path d="M2 34L40 4l38 30"/><path d="M12 26v40h20V44h16v22h20V26"/></svg>
        <h3>Mietrecht /<br>Wohnungs-<br>eigentumsrecht</h3>
      </div>
      <p>Ob zu Mietverträgen, Mieterhöhungen, Kündigungen und Räumungen, wir beraten und vertreten Vermieter, Mieter und Wohnungseigentümer.</p>
    </article>
  </div>
</section>

<section class="team">
  <h2 class="serif">Persönlich. Kompetent. Für Sie da.</h2>
  <div class="eyebrow">Kanzlei am Lindenhof</div>
  <div class="people">
    <div class="person">
      <div class="portrait" role="img" aria-label="Porträt Matthias Korwen" style="background:linear-gradient(180deg,#2a2a2a,#151515)"></div>
      <h3>Matthias Korwen</h3>
      <div class="role">Rechtsanwalt<br>Fachanwalt für Familienrecht</div>
      <a class="more">Profil ansehen &rarr;</a>
    </div>
    <div class="person">
      <div class="portrait" role="img" aria-label="Porträt Stefan P. Alberting" style="background:linear-gradient(180deg,#f2f2f2,#2c3140)"></div>
      <h3>Stefan P. Alberting</h3>
      <div class="role">Rechtsanwalt<br>(Freier Mitarbeiter)</div>
      <a class="more">Profil ansehen &rarr;</a>
    </div>
    <div class="person">
      <div class="portrait" role="img" aria-label="Porträt Brigitte Sommerfeld" style="background:linear-gradient(180deg,#e8e6e0,#233040)"></div>
      <h3>Brigitte Sommerfeld</h3>
      <div class="role">Rechtsanwältin und<br>Fachanwältin für Arbeitsrecht,<br>Verkehrsrecht und Erbrecht</div>
      <a class="more">Profil ansehen &rarr;</a>
    </div>
    <div class="person">
      <div class="portrait" role="img" aria-label="Porträt Reinhard Lobmair" style="background:linear-gradient(180deg,#efefef,#2a2a2e)"></div>
      <h3>Reinhard Lobmair</h3>
      <div class="role">Rechtsanwalt<br>(Freier Mitarbeiter)</div>
      <a class="more">Profil ansehen &rarr;</a>
    </div>
  </div>
  <a class="btn btn-beige all">Alle Anwälte anzeigen</a>
</section>

<section class="reviews">
  <div class="rv-intro">
    <h2 class="serif">Vertrauen durch<br>Erfahrung.</h2>
    <div class="label">EXCELENT</div>
    <svg width="164" height="26" viewBox="0 0 164 26" fill="var(--star)"><g id="s"><path d="M13 1l3.6 8 8.4.8-6.4 5.6 1.9 8.4L13 19.5 5.5 23.8l1.9-8.4L1 9.8l8.4-.8z"/></g><use href="#s" x="34"/><use href="#s" x="68"/><use href="#s" x="102"/><use href="#s" x="136"/></svg>
    <div class="based">Based on <b>529</b> reviews</div>
    <div class="platform"><span></span>Rezensio</div>
  </div>
  <svg class="arrow" style="left:394px" width="30" height="56" viewBox="0 0 30 56" fill="none" stroke="var(--beige)" stroke-width="2.5"><path d="M28 2L3 28l25 26"/></svg>
  <article class="review" style="left:432px">
    <svg width="164" height="26" viewBox="0 0 164 26" fill="var(--star)"><use href="#s"/><use href="#s" x="34"/><use href="#s" x="68"/><use href="#s" x="102"/><use href="#s" x="136"/></svg>
    <p>Top Anwalt und ein sehr einfühlsamer Mensch. Habe mich wirklich sehr wohl und richtig aufgehoben bei Ihm gefühlt. Nimmt sich Zeit auch wenn er andere Termine hat. Mit Themen die er nicht zu 100% weiß, liest er sich ein... Sehr sozialer und unkomplizierter Kontakt. Weiter so!</p>
    <div class="by">von A. P.</div>
  </article>
  <article class="review" style="left:777px">
    <svg width="164" height="26" viewBox="0 0 164 26" fill="var(--star)"><use href="#s"/><use href="#s" x="34"/><use href="#s" x="68"/><use href="#s" x="102"/><use href="#s" x="136"/></svg>
    <p>Ich war geschädigte eines Autounfalls, der Unfallverursacher wollte dies aber nicht einsehen. Somit musste ich einen Anwalt hinzuziehen. Herr Korwen war sehr aufschlussreich und hat die Sache recht schnell und unkompliziert für mich geklärt. Ich kann Ihn nur weiterempfehlen. ...</p>
    <div class="by">von G. M.</div>
  </article>
  <svg class="arrow" style="left:1122px" width="30" height="56" viewBox="0 0 30 56" fill="none" stroke="var(--beige)" stroke-width="2.5"><path d="M2 2l25 26L2 54"/></svg>
</section>

<footer class="contact">
  <h2 class="serif">Wir sind für Sie da.</h2>
  <p class="lead">Nehmen Sie Kontakt mit uns auf und vereinbaren Sie einen Termin für eine unverbindliche Erstberatung.</p>
  <a class="btn btn-beige">Erstberatung anfragen</a>
  <div class="channels">
    <div><svg width="24" height="24" viewBox="0 0 24 24" fill="#fff"><path d="M5 1l4 5-2 3c1 3 4 6 7 7l3-2 5 4-2 4c-9 1-20-10-19-19z"/></svg>0831 - 540 271 80</div>
    <div><svg width="24" height="18" viewBox="0 0 24 18" fill="none" stroke="#fff" stroke-width="2"><rect x="1" y="1" width="22" height="16"/><path d="M1 1l11 9 11-9"/></svg>info@kanzlei-lindenhof.de</div>
  </div>
  <div class="address">
    Kanzlei am Lindenhof<br>Lindenweg 14<br>87439 Kempten<br>
    <a>Anfahrt auf Kartenportal</a>
  </div>
</footer>

</body>
</html>
```